New Business Card Design Project

We require a business card design for Vexalund, a newly established Indian company.
Our focus is on the development, manufacturing, and export of a diverse array of pharmaceutical products on a global scale. The card should convey a professional appearance, as our primary markets are in Africa, China, and Southeast Asian nations.
We envision a two-sided business card, with the reverse side dedicated to a logo set against a solid color or an elegantly designed pattern. The corners should be rounded. We would appreciate seeing both horizontal and vertical design options. We trust the designer to utilize their expertise in creating this design.

The content for the business card is included in the attached Word file.

Target Market(s)

Our primary markets are in Africa, China, and Southeast Asian, Latin America, Maldives, Sri Lanka

Industry/Entity Type

Pharmaceutical Manufacturing and Export

Contact Information for Business Card

Colors

Designer to choose colors to be used in the design.

Requirements
Must have
• The reverse side of the business card features solely the logo along with the tagline, "Health in Motion."
Should not have
• The logo should not exceed two instances, encompassing both the front and back sides of the card.

```html
<!DOCTYPE html>
<html lang="en">
<head>
<meta charset="utf-8">
<title>Vexalund Business Card</title>
<link rel="stylesheet" href="https://fonts.googleapis.com/css2?family=Karla:wght@400;500;700&display=swap">
<style>
  :root {
    --stage: #2a2a2a;
    --brand-blue: #229fd6;
    --brand-blue-deep: #1d8dc2;
    --accent-red: #e05238;
    --paper: #f1f1f1;
    --paper-shade: #d9d9d9;
    --ink: #2e2e2e;
    --white: #ffffff;
  }
  html, body {
    margin: 0;
    padding: 0;
    width: 1200px;
    height: 1138px;
    overflow: hidden;
    background: var(--stage);
    font-family: "Karla", sans-serif;
  }
  .canvas {
    position: relative;
    width: 1200px;
    height: 1138px;
  }
  .card {
    position: absolute;
    border-radius: 16px;
    overflow: hidden;
  }
  .card svg { display: block; }
  .card--front { left: 273px; top: 185px; width: 625px; height: 377px; }
  .card--back  { left: 275px; top: 607px; width: 620px; height: 376px; }
  .brand-name { font-family: "Karla", sans-serif; font-weight: 700; fill: var(--white); }
  .tagline { font-family: "Karla", sans-serif; font-weight: 400; fill: var(--white); opacity: .9; }
  .web-line { font-family: "Karla", sans-serif; font-weight: 400; fill: var(--white); opacity: .85; }
  .person-name { font-family: "Karla", sans-serif; font-weight: 700; fill: var(--brand-blue); }
  .person-role, .contact-text, .address-text { font-family: "Karla", sans-serif; font-weight: 400; fill: var(--ink); }
</style>
</head>
<body>
<main class="canvas">

  <section class="card card--front" aria-label="Card reverse side">
    <svg width="625" height="377" viewBox="0 0 625 377">
      <defs>
        <linearGradient id="frontFill" x1="0" y1="0" x2="0" y2="1">
          <stop offset="0" stop-color="#26a2d9"/>
          <stop offset="1" stop-color="#1f93c8"/>
        </linearGradient>
      </defs>
      <rect width="625" height="377" fill="url(#frontFill)"/>
      <text class="brand-name" x="313" y="206" font-size="88" text-anchor="middle" textLength="396" lengthAdjust="spacingAndGlyphs">Vexalund</text>
      <text class="tagline" x="313" y="225" font-size="15" text-anchor="middle" textLength="392" lengthAdjust="spacing">HEALTH IN MOTION</text>
      <g class="web-rule" stroke="#ffffff" stroke-opacity=".7" stroke-width="1" fill="none">
        <circle cx="50" cy="346" r="3"/>
        <line x1="53" y1="346" x2="180" y2="346"/>
        <line x1="446" y1="346" x2="574" y2="346"/>
        <circle cx="577" cy="346" r="3"/>
      </g>
      <text class="web-line" x="313" y="351" font-size="15" text-anchor="middle" textLength="235" lengthAdjust="spacing">www.vexalund.com</text>
    </svg>
  </section>

  <section class="card card--back" aria-label="Card front side with contact details">
    <svg width="620" height="376" viewBox="0 0 620 376">
      <defs>
        <linearGradient id="paperFill" x1="0" y1="0" x2="0.3" y2="1">
          <stop offset="0" stop-color="#f4f4f4"/>
          <stop offset="1" stop-color="#d6d6d6"/>
        </linearGradient>
        <linearGradient id="panelFill" x1="0" y1="0" x2="0" y2="1">
          <stop offset="0" stop-color="#26a2d9"/>
          <stop offset="1" stop-color="#1f95cb"/>
        </linearGradient>
      </defs>
      <rect width="620" height="376" fill="url(#paperFill)"/>
      <path class="accent-arc" d="M0,0 L269,0 Q404,198 287,376 L0,376 Z" fill="var(--accent-red)"/>
      <path class="brand-panel" d="M0,0 L261,0 Q403,198 253,376 L0,376 Z" fill="url(#panelFill)"/>

      <text class="brand-name" x="164" y="207" font-size="54" text-anchor="middle" textLength="230" lengthAdjust="spacingAndGlyphs">Vexalund</text>

      <text class="person-name" x="373" y="110" font-size="26">Rohan K. Desai</text>
      <text class="person-role" x="373" y="135" font-size="16">CEO, Vexalund</text>

      <g class="contact-icons" fill="var(--accent-red)">
        <g class="icon-phone" transform="translate(375,173)">
          <path d="M0,4 Q7,-1 14,4 L14,6 L10,6 L10,4 Q7,3 4,4 L4,6 L0,6 Z"/>
          <rect x="2" y="7" width="10" height="6" rx="1"/>
        </g>
        <g class="icon-mail" transform="translate(375,197)">
          <rect x="0" y="0" width="14" height="10" rx="1"/>
          <path d="M0.5,0.5 L7,6 L13.5,0.5" stroke="#f1f1f1" stroke-width="1.3" fill="none"/>
        </g>
        <g class="icon-globe" transform="translate(382,226)" fill="none" stroke="var(--accent-red)" stroke-width="1.4">
          <circle r="6.5"/>
          <ellipse rx="3" ry="6.5"/>
          <line x1="-6.5" y1="0" x2="6.5" y2="0"/>
        </g>
      </g>
      <text class="contact-text" x="403" y="185" font-size="16">+91-9800012345</text>
      <text class="contact-text" x="403" y="208" font-size="16">rdesai@vexalund.com</text>
      <text class="contact-text" x="403" y="231" font-size="16">https://vexalund.com</text>

      <text class="address-text" x="373" y="261" font-size="16">12, Lotus Park Colony,</text>
      <text class="address-text" x="373" y="283" font-size="16">Nagpur-440010 (INDIA)</text>
    </svg>
  </section>

</main>
</body>
</html>
```